Business cards for Harbourline Supply Pty Ltd that import building products into Australia from China
Target Market(s)
Business to Business
Industry/Entity Type
Business
Contact Information for Business Card
Front: Logo and Business Name
Rear:
Desmond Varrick
General Manager
Mobile: 0427 561 394
email: dessie@harbourlinesupply.com.au
alternative email: dessie@outbackworks.com.au
web: www.harbourlinesupply.com.au
Adelaide, Brisbane and Darwin
Colors
ec1f27
fbee3d

```html
<!DOCTYPE html>
<html lang="en">
<head>
<meta charset="utf-8">
<title>Harbourline Supply – Business Cards</title>
<link href="https://fonts.googleapis.com/css2?family=Roboto:wght@300;400;700&display=swap" rel="stylesheet">
<style>
  :root {
    --brand-red: #ec1f27;
    --brand-yellow: #fbee3d;
    --card-yellow: #ffdd00;
    --white: #ffffff;
    --backdrop: #e6e4e0;
  }
  * { box-sizing: border-box; margin: 0; padding: 0; }
  html, body {
    width: 1200px;
    height: 900px;
    overflow: hidden;
    background: var(--backdrop);
    font-family: "Roboto", Arial, sans-serif;
  }
  .sheet {
    width: 1200px;
    height: 900px;
    display: flex;
    flex-direction: column;
    align-items: center;
    justify-content: center;
    gap: 40px;
  }
  .card {
    width: 640px;
    height: 390px;
    box-shadow: 0 6px 18px rgba(0,0,0,0.18);
    position: relative;
  }
  .card--rear {
    background: var(--brand-red);
    color: var(--white);
    display: flex;
    flex-direction: column;
    justify-content: center;
    padding-left: 150px;
  }
  .contact-name {
    font-weight: 700;
    font-size: 30px;
    letter-spacing: 0.5px;
    text-transform: uppercase;
    line-height: 1;
    padding-left: 36px;
  }
  .contact-title {
    font-weight: 400;
    font-size: 19px;
    text-transform: uppercase;
    line-height: 1.2;
    padding-left: 64px;
    margin-bottom: 30px;
  }
  .contact-list {
    list-style: none;
    font-size: 21px;
    line-height: 1.3;
  }
  .contact-list li {
    display: grid;
    grid-template-columns: 96px auto;
    margin-bottom: 12px;
  }
  .contact-list li:last-child { margin-bottom: 0; }
  .contact-label {
    color: var(--card-yellow);
    text-align: right;
    padding-right: 8px;
  }
  .contact-value span { display: block; }
  .card--front {
    background: var(--card-yellow);
    display: flex;
    align-items: center;
    justify-content: center;
  }
  .brand-name {
    color: var(--brand-red);
    font-weight: 300;
    font-size: 64px;
    letter-spacing: 1px;
    text-transform: lowercase;
  }
</style>
</head>
<body>
  <main class="sheet">
    <section class="card card--rear" aria-label="Business card rear">
      <h1 class="contact-name">Desmond Varrick</h1>
      <p class="contact-title">General Manager</p>
      <ul class="contact-list">
        <li><span class="contact-label">Mobile:</span><span class="contact-value">0427 561 394</span></li>
        <li><span class="contact-label">Email:</span><span class="contact-value"><span>dessie@harbourlinesupply.com.au</span><span>dessie@outbackworks.com.au</span></span></li>
        <li><span class="contact-label">Website:</span><span class="contact-value">www.harbourlinesupply.com.au</span></li>
      </ul>
    </section>
    <section class="card card--front" aria-label="Business card front">
      <p class="brand-name">harbourline supply</p>
    </section>
  </main>
</body>
</html>
```